Business card for acupunctist in Melbourne. Specialises in Fertility, pre and post natal care, pain

I am looking for a business card which is going to catch people eyes. Two sided, one side in a muted colour (keeping it feminine) (pink or yellow???)maybe with a little simple logo or picture, the other side I was thinking white with 3 colours (pink grey and yellow... Had these in mind.
Info on the card
Mirren Costa Acupuncture

Dr Mirren Costa (TCM Acupuncture)
Acupuncture for balancing body and mind.
Willowmere Therapeutics
14 Ferndale Road, Oakhurst 3071.
94726151
0428319574
Mirrentcm@quillpost.net

Some other little logo/ designs I have liked are as follows:
http://www.dorotheabrisklac.net/rates-and-insurance/
http://www.rosalindpeverell.net/
http://www.tz-acupuncture.example.uk/

Target Market(s)

professional women, people in pain, active people, people seeking a healthy lifefstyle.

Industry/Entity Type

Business

Font styles to use
Serif
Sans Serif

Colors
eea4c8
fde08a
aaaaaa

Requirements
Must have
• Must be eye catching, but not too loud and busy. Subltle is good. Simple is also good. The logo could be something that represents growth and health and nurturing. Again not too elaborate, very simple.
Thankyou
Should not have
• Electric colours, crazy fonts, Pictures of yin and yang, candles, or bodies.

```html
<!DOCTYPE html>
<html lang="en">
<head>
<meta charset="utf-8">
<title>Mirren Costa Acupuncture – Business Card</title>
<link rel="stylesheet" href="https://fonts.googleapis.com/css2?family=Tinos&family=Open+Sans:wght@400&display=swap">
<style>
  :root {
    --canvas: #e9e6e6;
    --card: #000000;
    --yellow: #f5e400;
    --pink: #f2c4d6;
    --pink-mark: #eea4c8;
    --grey-band: #8e8585;
    --white: #ffffff;
    --serif: "Tinos", "Times New Roman", serif;
    --sans: "Open Sans", Arial, sans-serif;
  }
  * { box-sizing: border-box; margin: 0; padding: 0; }
  html, body { width: 1200px; height: 900px; overflow: hidden; }
  body {
    background: var(--canvas);
    display: flex;
    flex-direction: column;
    align-items: center;
    justify-content: center;
    gap: 40px;
  }
  .card {
    position: relative;
    width: 700px;
    height: 400px;
    background: var(--card);
    overflow: hidden;
  }

  /* Info side */
  .info-side .brand-title {
    position: absolute;
    top: 38px; right: 40px;
    font-family: var(--serif);
    font-size: 34px;
    letter-spacing: -1px;
    color: var(--yellow);
    text-transform: uppercase;
    text-align: center;
  }
  .info-side .brand-sub {
    display: block;
    font-family: var(--sans);
    font-size: 13px;
    letter-spacing: 0.3px;
    color: var(--white);
    text-transform: none;
    margin-top: 2px;
  }
  .contact-list {
    position: absolute;
    top: 140px; left: 40px;
    list-style: none;
    font-family: var(--sans);
    font-size: 13px;
    color: var(--white);
  }
  .contact-list li {
    display: flex;
    align-items: center;
    gap: 10px;
    height: 22px;
  }
  .contact-list svg { width: 13px; height: 13px; flex: none; }
  .practitioner {
    position: absolute;
    top: 232px; right: 60px;
    text-align: center;
  }
  .practitioner .name {
    font-family: var(--serif);
    font-size: 30px;
    letter-spacing: -1px;
    color: var(--yellow);
    text-transform: uppercase;
  }
  .practitioner .role {
    font-family: var(--sans);
    font-size: 13px;
    color: var(--white);
  }
  .grey-band {
    position: absolute;
    left: 0; right: 0; bottom: 0;
    height: 62px;
    background: var(--grey-band);
  }

  /* Brand side */
  .brand-side .mark {
    position: absolute;
    top: 70px; left: 50%;
    transform: translateX(-50%);
    width: 60px; height: 60px;
    border-radius: 50%;
    background: var(--pink-mark);
  }
  .brand-side .wordmark {
    position: absolute;
    top: 160px; left: 0; right: 0;
    text-align: center;
    font-family: var(--serif);
    font-size: 44px;
    letter-spacing: -1.5px;
    color: var(--pink);
    text-transform: uppercase;
  }
  .brand-side .tagline {
    position: absolute;
    top: 216px; left: 0; right: 0;
    text-align: center;
    font-family: var(--serif);
    font-size: 18px;
    color: var(--pink);
  }
  .brand-side .yellow-rule {
    position: absolute;
    left: 0; right: 0;
    top: 300px;
    height: 8px;
    background: var(--yellow);
  }
</style>
</head>
<body>

  <section class="card info-side">
    <h1 class="brand-title">Mirren Costa Acupuncture
      <span class="brand-sub">Willowmere Therapeutics</span>
    </h1>

    <ul class="contact-list">
      <li>
        <svg viewBox="0 0 12 12"><path d="M6 1a3.5 3.5 0 0 1 3.5 3.5C9.5 7 6 11 6 11S2.5 7 2.5 4.5A3.5 3.5 0 0 1 6 1z" fill="none" stroke="#f5e400" stroke-width="1.2"/><circle cx="6" cy="4.5" r="1.2" fill="#f5e400"/></svg>
        14 Ferndale Road, Oakhurst 3071
      </li>
      <li>
        <svg viewBox="0 0 12 12"><rect x="1" y="2.5" width="10" height="7" fill="none" stroke="#f5e400" stroke-width="1.2"/><path d="M1 2.5l5 4 5-4" fill="none" stroke="#f5e400" stroke-width="1.2"/></svg>
        Mirrentcm@quillpost.net
      </li>
      <li>
        <svg viewBox="0 0 12 12"><path d="M3 1.5l2 2.2-1.2 1.5c.6 1.3 1.6 2.3 2.9 2.9l1.5-1.2 2.3 2-1.3 1.6C5.5 10.2 1.8 6.5 1.4 2.8z" fill="#f5e400"/></svg>
        94726151
      </li>
      <li>
        <svg viewBox="0 0 12 12"><rect x="3" y="1" width="6" height="10" rx="1" fill="none" stroke="#f5e400" stroke-width="1.2"/><circle cx="6" cy="9" r=".7" fill="#f5e400"/></svg>
        0428319574
      </li>
    </ul>

    <div class="practitioner">
      <p class="name">Dr Mirren Costa</p>
      <p class="role">TCM Acupuncture</p>
    </div>

    <div class="grey-band"></div>
  </section>

  <section class="card brand-side">
    <div class="mark"></div>
    <p class="wordmark">Mirren Costa Acupuncture</p>
    <p class="tagline">Acupuncture for balancing body and mind</p>
    <div class="yellow-rule"></div>
  </section>

</body>
</html>
```